Ledgerwise Forge - WordPress Theme & Logo

Design a logo and Wordpress website design for Ledgerwise Forge. Ledgerwise Forge provides cryptocurrency development services to clients who need a team to create & continue developing a new cryptocurrency or who want to replace their current cryptocurrency development team. more details in the attached document.
Updates

Target Market(s)

Entrepreneurs who are building a business / platform that makes use of an underlying cryptocurrency.

Logo Text

LF or Ledgerwise Forge

Coding

Coded - Design and coding required

Font styles to use
Sans Serif

Requirements
Must have
• Professional logo, complete coded Wordpress theme for all pages, containing all specified links and buttons
Nice to have
• It would be nice if the buttons that are meant to integrate with Dealtrail contain the necessary code for that. I can provide any necessary Dealtrail details from my account.
Should not have
• Slow loading time

```html
<!DOCTYPE html>
<html lang="en">
<head>
<meta charset="utf-8">
<title>Ledgerwise Forge — Cryptocurrency Development</title>
<link rel="stylesheet" href="https://fonts.googleapis.com/css2?family=Rubik:wght@500;700;800&family=Nunito+Sans:wght@300;400;600;700&display=swap">
<style>
:root{
  --blue:#3a78f0;
  --blue-deep:#1f66e6;
  --indigo:#4455e6;
  --royal:#3d5ee8;
  --logo-blue:#2f6ae8;
  --ink:#111418;
  --text:#3c4048;
  --muted:#5d6068;
  --pale:#f1f4f9;
  --services-bg:#e3ebf7;
  --footer:#15171b;
  --white:#ffffff;
  --head:"Rubik",sans-serif;
  --body:"Nunito Sans",sans-serif;
}
*{box-sizing:border-box;margin:0;padding:0}
html,body{width:1200px;height:3338px;overflow:hidden}
body{font-family:var(--body);color:var(--text);background:var(--white);position:relative}
a{color:inherit;text-decoration:none}

.site-header{height:100px;display:flex;align-items:center;justify-content:space-between;padding:0 97px 0 100px;background:var(--white)}
.brand{display:flex;align-items:center;gap:12px;font-family:var(--head);font-weight:700;font-size:23px;color:var(--logo-blue)}
.brand-dot{width:44px;height:44px;border-radius:50%;border:3px solid var(--logo-blue)}
.main-nav{display:flex;gap:54px;font-size:14.5px;font-weight:600;color:var(--ink)}

.hero{position:relative;height:592px;background:radial-gradient(ellipse at 50% 38%,#56607a 0%,#2a3040 35%,#161b26 70%,#0f1219 100%);color:var(--white);text-align:center;overflow:hidden}
.hero-photo{position:absolute;inset:0}
.hero h1{position:relative;padding-top:148px;font-family:var(--head);font-weight:800;font-size:61px;letter-spacing:.5px}
.hero .lead{position:relative;margin-top:4px;font-size:32px;font-weight:300}
.hero-actions{position:relative;margin-top:26px;display:flex;justify-content:center;gap:9px}
.btn{display:inline-block;font-family:var(--body);font-weight:700;text-transform:uppercase;letter-spacing:.2px}
.btn-hero{height:44px;line-height:44px;padding:0 17px;font-size:15.5px;color:var(--white)}
.btn-indigo{background:var(--indigo)}
.btn-blue{background:var(--blue)}
.slider-arrow{position:absolute;top:230px;width:20px;height:34px}
.slider-arrow.prev{left:34px}
.slider-arrow.next{right:34px}
.hero-curve{position:absolute;left:0;bottom:0;width:1200px;height:60px}

.intro{height:196px;background:linear-gradient(180deg,#eceef2,#f3f4f7);text-align:center;padding-top:34px}
.intro p{width:780px;margin:0 auto;font-size:17.5px;line-height:30px;color:#4a4d55;font-weight:400}

.section-title{font-family:var(--head);font-weight:800;font-size:34px;color:var(--ink);text-align:center;text-transform:uppercase;letter-spacing:.3px}

.why{height:532px;background:var(--pale);padding-top:72px}
.features{display:flex;gap:29px;padding:0 100px;margin-top:58px}
.feature{position:relative;width:314px;height:204px;margin-top:60px;border:3px solid #5a8cf5;color:var(--white);text-align:center;padding-top:58px}
.feature-tab{position:absolute;left:50%;top:-64px;transform:translateX(-50%);width:146px;height:73px;border-radius:73px 73px 0 0;border:3px solid #5a8cf5;border-bottom:none;display:flex;align-items:center;justify-content:center;padding-top:12px}
.feature h3{font-family:var(--body);font-weight:600;font-size:28px}
.feature p{margin:10px auto 0;width:250px;font-size:15.5px;line-height:21px}
.feature.value,.feature.value .feature-tab{background:#3b80f0}
.feature.support,.feature.support .feature-tab{background:#2470e8}
.feature.commitment,.feature.commitment .feature-tab{background:#4352e4}

.about{height:418px;background:linear-gradient(100deg,#2d6ee8 0%,#2a6ae6 60%,#3d7ff0 100%);color:var(--white);text-align:center;padding-top:78px;position:relative}
.about-photo{position:absolute;inset:0;background:radial-gradient(ellipse at 80% 50%,rgba(255,255,255,.14),transparent 60%)}
.about .section-title{color:var(--white);position:relative}
.about p{position:relative;width:690px;margin:14px auto 0;font-size:15.5px;line-height:30px}
.btn-light{position:relative;margin-top:24px;background:var(--white);color:var(--blue-deep);height:44px;line-height:44px;padding:0 21px;font-size:15.5px}

.testimonials{height:475px;background:linear-gradient(180deg,#fff 0%,#fbfcfe 70%,#eef2f8 100%);padding-top:66px}
.quotes{display:flex;gap:29px;padding:0 100px;margin-top:44px}
.quote{position:relative;width:314px;height:192px;margin-top:53px;background:var(--white);box-shadow:0 2px 10px rgba(0,0,0,.14);text-align:center;padding-top:56px}
.avatar{position:absolute;left:50%;top:-53px;transform:translateX(-50%);width:103px;height:103px;border-radius:50%;background:linear-gradient(160deg,#8a7a6c,#3f4650)}
.quote h4{font-family:var(--body);font-weight:600;font-size:19px;color:var(--ink)}
.quote p{margin:6px auto 0;width:238px;font-size:11.5px;line-height:18px;color:var(--muted)}

.services{height:695px;background:var(--services-bg);padding-top:66px;text-align:center}
.service-list{display:flex;gap:29px;padding:0 100px;margin-top:44px;text-align:center}
.service{width:314px}
.service-photo{height:205px}
.service h3{font-family:var(--body);font-weight:700;font-size:22px;color:var(--ink);line-height:26px;margin-top:22px}
.service.tall h3{margin-top:14px}
.service p{margin-top:8px;font-size:14.5px;line-height:21px;color:var(--text);padding:0 10px}
.btn-cta{margin-top:62px;background:var(--blue);color:var(--white);height:56px;line-height:56px;padding:0 24px;font-size:18px}

.site-footer{height:330px;background:radial-gradient(ellipse at 70% 40%,#22252b,var(--footer) 70%);color:var(--white);position:relative}
.footer-brand{position:absolute;left:100px;top:68px;width:320px}
.footer-brand .brand{color:var(--white)}
.footer-brand .brand-dot{border-color:var(--white)}
.footer-brand p{margin-top:16px;font-size:11px;line-height:21px}
.footer-col{position:absolute;top:58px}
.footer-col h5{font-family:var(--head);font-weight:700;font-size:19px;margin-bottom:12px}
.footer-col li{list-style:none;font-size:13px;line-height:30px}
.col-links{left:490px}
.col-resources{left:641px}
.newsletter{left:832px}
.signup{display:flex;margin-top:2px}
.signup span{width:166px;height:38px;background:var(--white);color:#333;font-size:15px;line-height:38px;padding-left:16px}
.signup b{width:102px;height:38px;background:var(--blue-deep);font-size:15px;line-height:38px;text-align:center;font-weight:600}
.socials{display:flex;gap:5px;margin-top:16px}
.socials i{display:block;width:36px;height:36px;border:1.5px solid var(--white);border-radius:50%;position:relative}
.socials i::after{content:"";position:absolute;left:14px;top:14px;width:6px;height:6px;border-radius:50%;background:var(--white)}
.footer-rule{position:absolute;left:0;right:0;top:268px;height:1px;background:#2c2f35}
.copyright{position:absolute;left:0;right:0;top:290px;text-align:center;font-size:11.5px}
.page-code{position:absolute;right:27px;top:290px;font-size:11.5px}
</style>
</head>
<body>

<header class="site-header">
  <a class="brand" href="#"><span class="brand-dot"></span>Ledgerwise Forge</a>
  <nav class="main-nav">
    <a href="#">About</a><a href="#">Testimonials</a><a href="#">Services</a><a href="#">Book a Consultation</a><a href="#">Blog</a>
  </nav>
</header>

<section class="hero">
  <div class="hero-photo" role="img" aria-label="Figure standing in a dark tunnel facing a large glowing coin-shaped doorway"></div>
  <h1>Your own cryptocurrency.</h1>
  <p class="lead">Secure, easy to use, and built by an expert team.</p>
  <div class="hero-actions">
    <a class="btn btn-hero btn-indigo" href="#">Download a free PDF</a>
    <a class="btn btn-hero btn-blue" href="#">Schedule free consultation</a>
  </div>
  <svg class="slider-arrow prev" viewBox="0 0 20 34"><path d="M18 2 3 17l15 15" fill="none" stroke="#fff" stroke-width="1.6"/></svg>
  <svg class="slider-arrow next" viewBox="0 0 20 34"><path d="M2 2l15 15L2 32" fill="none" stroke="#fff" stroke-width="1.6"/></svg>
  <svg class="hero-curve" viewBox="0 0 1200 60" preserveAspectRatio="none"><path d="M0 60C300 18 500 0 640 0S1000 22 1200 60Z" fill="#eceef2"/></svg>
</section>

<section class="intro">
  <p>Ledgerwise Forge adds professionalism to cryptocurrency development. Our done-for-you service covers everything from development and IT operations to ongoing support. You have access to a full team, for less than the typical cost of a single developer.</p>
</section>

<section class="why">
  <h2 class="section-title">Why choose Ledgerwise Forge</h2>
  <div class="features">
    <div class="feature value">
      <div class="feature-tab"><svg width="52" height="48" viewBox="0 0 52 48" fill="none" stroke="#fff" stroke-width="1.6"><circle cx="16" cy="9" r="5"/><circle cx="26" cy="7" r="5"/><circle cx="36" cy="9" r="5"/><path d="M8 26c0-7 6-10 8-10s8 3 8 10M18 24c0-8 5-11 8-11s8 3 8 11M28 26c0-7 6-10 8-10s8 3 8 10"/><path d="M3 34l10 0 8 4h14l12-6M3 46h10l10-4h10"/></svg></div>
      <h3>Value</h3><p>A team of experts, regular updates, and fixed costs</p>
    </div>
    <div class="feature support">
      <div class="feature-tab"><svg width="46" height="52" viewBox="0 0 46 52" fill="none" stroke="#fff" stroke-width="1.6"><circle cx="23" cy="17" r="10"/><path d="M11 17a12 12 0 0 1 24 0M23 31h6M3 50c0-11 9-17 20-17s20 6 20 17Z"/></svg></div>
      <h3>Support</h3><p>Receive advice and other services, beyond development.</p>
    </div>
    <div class="feature commitment">
      <div class="feature-tab"><svg width="60" height="46" viewBox="0 0 60 46" fill="none" stroke="#fff" stroke-width="1.6"><path d="M2 14 12 4l8 8-10 10ZM58 14 48 4l-8 8 10 10ZM16 18l10-6h10l10 10-16 16-14-14M24 22l8-6M22 28l6 6M26 24l6 6M30 20l6 6"/></svg></div>
      <h3>Commitment</h3><p>Enjoy regular updates and new features.</p>
    </div>
  </div>
</section>

<section class="about">
  <div class="about-photo" role="img" aria-label="Hands over a laptop with faint market charts and figures"></div>
  <h2 class="section-title">About Ledgerwise Forge</h2>
  <p>In addition to creating and enhancing cryptocurrencies for clients, the Ledgerwise Forge team has been running the Corvane cryptocurrency since 2017. We prefer long-term relationships, enabling us to deliver the very highest quality and giving you peace of mind that you've got a professional and trustworthy team at your side.</p>
  <a class="btn btn-light" href="#">Learn more</a>
</section>

<section class="testimonials">
  <h2 class="section-title">Client testimonials</h2>
  <div class="quotes">
    <div class="quote"><div class="avatar" role="img" aria-label="Portrait of the client"></div><h4>Marisol Trevanne</h4><p>Lorem Ipsum is simply dummy text of the printing and typesetting industry. Lorem Ipsum has been the industry's standard dummy text ever since the 1500s</p></div>
    <div class="quote"><div class="avatar" role="img" aria-label="Portrait of the client"></div><h4>Finibus Bonorum</h4><p>Lorem Ipsum is simply dummy text of the printing and typesetting industry. Lorem Ipsum has been the industry's standard dummy text ever since the 1500s</p></div>
    <div class="quote"><div class="avatar" role="img" aria-label="Portrait of the client"></div><h4>Voluptatibus Maiores</h4><p>Lorem Ipsum is simply dummy text of the printing and typesetting industry. Lorem Ipsum has been the industry's standard dummy text ever since the 1500s</p></div>
  </div>
</section>

<section class="services">
  <h2 class="section-title">Services</h2>
  <div class="service-list">
    <div class="service tall">
      <div class="service-photo" role="img" aria-label="Hands around a table with glowing currency symbols" style="background:linear-gradient(135deg,#0c3a55,#1e8a9a 50%,#0b2c48)"></div>
      <h3>Blockchain Creation<br>and Launch</h3>
      <p>Temporibus autem quibusdam et aut officiis debitis aut rerum necessitatibus saepe eveniet ut et voluptates repudiandae sint et molestiae non recusandae.</p>
    </div>
    <div class="service">
      <div class="service-photo" role="img" aria-label="Hand holding a phone in blue light" style="background:linear-gradient(135deg,#0a1f5a,#2a5bd6 55%,#0a1a48)"></div>
      <h3>Basic</h3>
      <p>Temporibus autem quibusdam et aut officiis debitis aut rerum necessitatibus saepe eveniet ut et voluptates repudiandae sint et molestiae non recusandae.</p>
    </div>
    <div class="service">
      <div class="service-photo" role="img" aria-label="Hand pointing at a glowing candlestick market chart" style="background:linear-gradient(135deg,#0a1a4a,#2157c8 55%,#0c2466)"></div>
      <h3>Mid-range</h3>
      <p>Temporibus autem quibusdam et aut officiis debitis aut rerum necessitatibus saepe eveniet ut et voluptates repudiandae sint et molestiae non recusandae.</p>
    </div>
  </div>
  <a class="btn btn-cta" href="#">Schedule a free consultation</a>
</section>

<footer class="site-footer">
  <div class="footer-brand">
    <a class="brand" href="#"><span class="brand-dot"></span>Ledgerwise Forge</a>
    <p>At vero eos et accusamus et iusto odio dignissimos ducimus qui blanditiis praesentium voluptatum deleniti atque corrupti quos dolores et quas molestias excepturi sint occaecati cupiditate non provident</p>
  </div>
  <div class="footer-col col-links"><h5>Links</h5><ul><li>Home</li><li>About</li><li>Feature</li><li>Pricing</li><li>Contact</li></ul></div>
  <div class="footer-col col-resources"><h5>Resources</h5><ul><li>Blog</li><li>Search</li><li>Terms &amp; Conditions</li><li>Privacy</li><li>Community</li></ul></div>
  <div class="footer-col newsletter">
    <h5>Get Our Newsletter</h5>
    <div class="signup"><span>Your email</span><b>SUBSCRIBE</b></div>
    <div class="socials"><i></i><i></i><i></i><i></i></div>
  </div>
  <div class="footer-rule"></div>
  <p class="copyright">© 2021 Ledgerwise Forge. All rights reserved.</p>
  <p class="page-code">C16</p>
</footer>

</body>
</html>
```